Corporate Design für logopädische Praxis
Zielgruppe
Ich gründe eine logopädische Praxis, die Sprachtherapie sowohl für Erwachsene als auch Kinder anbietet und damit ein Logo benötigt, das jede Altersgruppe anspricht und 'Lindenhof' als fachliche und menschliche Qualitätszeit interpretiert.
Aufgabenstellung
Ich bevorzuge ein klares Design, welches das Wortspiel der 'Lindenhof' im Idealfall aufgreift und den Patienten vermittelt, dass sowohl die fachliche Qualität der Behandlung als auch die Ebene von Empathie und Patientenorientierung im zwischenmenschlichen Umgang für die Praxis zentral sind.

```html
<!DOCTYPE html>
<html lang="de">
<head>
<meta charset="utf-8">
<title>Lindenhof – Praxis für Logopädie</title>
<link href="https://fonts.googleapis.com/css2?family=Nunito:wght@300;400&family=Montserrat:wght@300;400&family=Roboto:wght@300&display=swap" rel="stylesheet">
<style>
  :root{
    --mauve:#a48ea8;
    --mauve-soft:#b9a3b6;
    --ink:#3c3c3c;
    --grey:#7a7a7a;
    --paper:#ffffff;
    --stage-light:#fafafa;
    --stage-dark:#404040;
    --bar:#ededed;
    --rule:#c9b9cc;
    --sign:#1f3f8a;
  }
  *{margin:0;padding:0;box-sizing:border-box}
  html,body{width:1200px;height:2760px;overflow:hidden}
  body{position:relative;background:var(--stage-dark);font-family:"Montserrat",sans-serif;color:var(--ink)}
  .hero{position:absolute;left:0;top:0;width:1200px;height:978px;background:var(--stage-light)}
  .brand{position:absolute;display:flex;flex-direction:column;align-items:flex-end;font-family:"Nunito",sans-serif;font-weight:300}
  .brand-name{display:flex;align-items:center;color:var(--mauve);line-height:1}
  .brand-dot{border-radius:50%;background:var(--mauve);flex:none}
  .brand-tag{color:var(--grey);line-height:1}
  .hero .brand{left:320px;top:440px}
  .hero .brand-name{font-size:108px;gap:22px}
  .hero .brand-dot{width:26px;height:26px}
  .hero .brand-tag{font-size:33px;letter-spacing:5px;margin-top:4px}

  .card{position:absolute;width:380px;height:245px;background:var(--paper)}
  .card-appointment{left:191px;top:1035px}
  .card-contact{left:628px;top:1035px}
  .appt-label{position:absolute;left:41px;top:26px;font-size:14px;color:var(--mauve);font-weight:300}
  .appt-lines{position:absolute;left:41px;top:51px;width:299px}
  .appt-lines span{display:block;height:23px;background:var(--bar);margin-bottom:8px}
  .card-appointment .brand{right:46px;top:188px}
  .card-appointment .brand-name{font-size:30px;gap:7px}
  .card-appointment .brand-dot{width:8px;height:8px}
  .card-appointment .brand-tag{font-size:8.5px;letter-spacing:1.5px;margin-top:1px}
  .card-contact .brand{left:38px;top:53px}
  .card-contact .brand-name{font-size:44px;gap:10px}
  .card-contact .brand-dot{width:11px;height:11px}
  .card-contact .brand-tag{font-size:13px;letter-spacing:2.2px;margin-top:2px}
  .card-person{position:absolute;left:34px;top:153px;font-size:10px;font-weight:300;color:var(--grey);line-height:1.45}
  .card-person .name{font-size:11px;color:var(--ink);letter-spacing:.3px}
  .card-person .addr{margin-top:24px}
  .contact-list{position:absolute;left:209px;top:150px;list-style:none;font-size:9.5px;font-weight:300;color:var(--grey)}
  .contact-list li{display:flex;align-items:center;gap:7px;height:16px}
  .ico{width:11px;height:11px;border:1px solid var(--mauve-soft);border-radius:50%;font-size:6px;display:flex;align-items:center;justify-content:center;color:var(--mauve);flex:none}

  .letter{position:absolute;left:130px;top:1327px;width:939px;height:1329px;background:var(--paper)}
  .letter .brand{right:74px;top:96px}
  .letter .brand-name{font-size:62px;gap:14px}
  .letter .brand-dot{width:15px;height:15px}
  .letter .brand-tag{font-size:20px;letter-spacing:3.2px;margin-top:3px}
  .sender-line{position:absolute;left:118px;top:264px;font-size:9px;font-weight:300;color:var(--grey)}
  .recipient{position:absolute;left:118px;top:285px;font-family:"Roboto",sans-serif;font-weight:300;font-size:15.5px;line-height:19px}
  .fold{position:absolute;left:0;width:23px;height:1px;background:#555}
  .fold-1{top:468px}.fold-2{top:939px}
  .letter-body{position:absolute;left:118px;top:466px;width:705px;font-family:"Roboto",sans-serif;font-weight:300;font-size:15.5px;line-height:18.9px}
  .letter-body p{margin-bottom:18.9px}
  .letter-body .salute{margin-bottom:38px}
  .letter-body .closing{margin-top:38px}
  .signature{position:absolute;left:118px;top:995px;width:150px;height:82px;background:linear-gradient(100deg,rgba(31,63,138,.12),rgba(31,63,138,.04))}
  .footer{position:absolute;left:118px;top:1184px;display:flex;font-size:11px;font-weight:300;color:var(--grey)}
  .footer-col{line-height:24px;padding:0 0 0 24px;border-left:1px solid var(--rule)}
  .footer-col:first-child{padding-left:0;border-left:none;width:166px}
  .footer-col:nth-child(2){width:162px}
  .footer-col:nth-child(3){width:240px}
  .footer-col li{list-style:none;display:flex;align-items:center;gap:10px}
</style>
</head>
<body>
  <section class="hero">
    <div class="brand">
      <div class="brand-name"><span class="brand-dot"></span>Lindenhof</div>
      <div class="brand-tag">Praxis für Logopädie</div>
    </div>
  </section>

  <article class="card card-appointment">
    <div class="appt-label">Ihr nächster Termin:</div>
    <div class="appt-lines"><span></span><span></span><span></span><span></span></div>
    <div class="brand">
      <div class="brand-name"><span class="brand-dot"></span>Lindenhof</div>
      <div class="brand-tag">Praxis für Logopädie</div>
    </div>
  </article>

  <article class="card card-contact">
    <div class="brand">
      <div class="brand-name"><span class="brand-dot"></span>Lindenhof</div>
      <div class="brand-tag">Praxis für Logopädie</div>
    </div>
    <div class="card-person">
      <div class="name">MAX MUSTERMANN</div>
      <div>Geschäftsführer</div>
      <div class="addr">Musterweg 13<br>54321 Musterdorf</div>
    </div>
    <ul class="contact-list">
      <li><span class="ico">t</span>+49 (0)1234 5 67 89-0</li>
      <li><span class="ico">f</span>+49 (0)1234 5 67 89-50</li>
      <li><span class="ico">m</span>+49 (0)123 4 56 78 90</li>
      <li><span class="ico">e</span>info@yourcompany.de</li>
      <li><span class="ico">w</span>yourcompany.de</li>
    </ul>
  </article>

  <article class="letter">
    <div class="brand">
      <div class="brand-name"><span class="brand-dot"></span>Lindenhof</div>
      <div class="brand-tag">Praxis für Logopädie</div>
    </div>
    <div class="sender-line">Your Company | Musterweg 13 | 54321 Musterdorf</div>
    <div class="recipient">Max Mustermann<br>Musterstr. 1<br>12345 Muster</div>
    <span class="fold fold-1"></span>
    <span class="fold fold-2"></span>
    <div class="letter-body">
      <p class="salute">Sehr geehrte Damen und Herren,</p>
      <p>Lorem ipsum dolor sit amet, consetetur sadipscing elitr, sed diam nonumy eirmod tempor invidunt ut labore et dolore magna aliquyam erat, sed diam voluptua. At vero eos et accusam et justo duo dolores et ea rebum. Stet clita kasd gubergren, no sea takimata sanctus est Lorem ipsum dolor sit amet. Lorem ipsum dolor sit amet, consetetur sadipscing elitr, sed diam nonumy eirmod tempor invidunt ut labore et dolore magna aliquyam erat, sed diam voluptua. At vero eos et accusam et justo duo dolores et ea rebum. Stet clita kasd gubergren, no sea takimata sanctus est Lorem ipsum dolor sit amet. Lorem ipsum dolor sit amet, consetetur sadipscing elitr, sed diam nonumy eirmod tempor invidunt ut labore et dolore magna aliquyam erat, sed diam voluptua. At vero eos et accusam et justo duo dolores et ea rebum. Stet clita kasd gubergren, no sea takimata sanctus est Lorem ipsum dolor sit amet.</p>
      <p>Duis autem vel eum iriure dolor in hendrerit in vulputate velit esse molestie consequat, vel illum dolore eu feugiat nulla facilisis at vero eros et accumsan et iusto odio dignissim qui blandit praesent luptatum zzril delenit augue duis dolore te feugait nulla facilisi. Lorem ipsum dolor sit amet, consectetuer adipiscing elit, sed diam nonummy nibh euismod tincidunt ut laoreet dolore magna aliquam erat volutpat.</p>
      <p>Ut wisi enim ad minim veniam, quis nostrud exerci tation ullamcorper suscipit lobortis nisl ut aliquip ex ea commodo consequat. Duis autem vel eum iriure dolor in hendrerit in vulputate velit esse molestie consequat, vel illum dolore eu feugiat nulla facilisis at vero eros et accumsan et iusto odio dignissim qui blandit praesent luptatum zzril delenit augue duis dolore te feugait nulla facilisi.</p>
      <p class="closing">Mit freundlichen Grüßen</p>
    </div>
    <div class="signature" role="img" aria-label="Handschriftliche Unterschrift"></div>
    <footer class="footer">
      <ul class="footer-col">
        <li><span class="ico">t</span>+49 (0)1234 5 67 89-0</li>
        <li><span class="ico">f</span>+49 (0)1234 5 67 89-50</li>
        <li><span class="ico">e</span>info@yourcompany.de</li>
        <li><span class="ico">w</span>yourcompany.de</li>
      </ul>
      <ul class="footer-col">
        <li>MAX MUSTERMANN</li>
        <li>Geschäftsführer</li>
        <li>Musterweg 13</li>
        <li>54321 Musterdorf</li>
      </ul>
      <ul class="footer-col">
        <li>Talsparkasse</li>
        <li>IBAN: DE43 XXXX 0110 XXXX 0481 XX</li>
        <li>BIC: KRXXDE55XXX</li>
        <li>Geschäftsführer: Max Mustermann</li>
      </ul>
      <ul class="footer-col">
        <li>Ust. ID: DE2XX9XX10X</li>
        <li>HRB 1XX4XX</li>
        <li>Amtsgericht Bergstadt</li>
        <li>Gesellschaftssitz: Wiesental</li>
      </ul>
    </footer>
  </article>
</body>
</html>
```